Business Card Design

We need a business card designed for our new company. Prefer a black card with white logo & writing.

Contact Information for Business Card

Ted Galloway, address: 7-4812 Fernhollow Road, Abbotsford, BC, V3K 8R2, Office Phone: 604-712-3390, Cell: 604-947-2164, Email: ted@resinworkshub.ca

Colors

Designer to choose only greyscale colors for use in the design.

```html
<!DOCTYPE html>
<html lang="en">
<head>
<meta charset="utf-8">
<title>Resinworks Hub — Business Card</title>
<link href="https://fonts.googleapis.com/css2?family=Poppins:wght@400;700&display=swap" rel="stylesheet">
<style>
  :root {
    --backdrop: #2a2a2a;
    --card: #0d0d0d;
    --ink: #ffffff;
    --ink-soft: #e6e6e6;
    --rule: #3a3a3a;
    --foil: #cfcfcf;
  }
  * { box-sizing: border-box; margin: 0; padding: 0; }
  html, body {
    width: 1200px; height: 900px; overflow: hidden;
    background: var(--backdrop);
    font-family: "Poppins", sans-serif;
  }
  .sheet {
    width: 1200px; height: 900px;
    display: flex; flex-direction: column;
    align-items: center; justify-content: center; gap: 40px;
  }
  .card {
    width: 700px; height: 400px;
    background: var(--card);
    border-radius: 28px;
    position: relative;
    color: var(--ink);
  }
  /* Contact side */
  .card--contact { display: flex; }
  .brand-panel {
    width: 47%;
    display: flex; align-items: center; justify-content: center;
    border-right: 1px solid var(--rule);
    margin: 70px 0;
  }
  .brand-name {
    font-weight: 700; font-size: 30px; letter-spacing: 0.5px;
    display: flex; align-items: center; gap: 12px;
    color: var(--ink);
    text-transform: uppercase; line-height: 1;
  }
  .brand-mark {
    width: 14px; height: 14px; border-radius: 50%;
    background: var(--ink);
    flex: none;
  }
  .details {
    flex: 1;
    padding: 88px 0 0 42px;
  }
  .details__name {
    font-weight: 700; font-size: 26px; letter-spacing: 0.5px;
    text-transform: uppercase; margin-bottom: 22px;
  }
  .details__list { list-style: none; }
  .details__item {
    display: flex; align-items: center; gap: 12px;
    font-size: 19px; line-height: 30px; color: var(--ink-soft);
  }
  .details__item svg { width: 18px; height: 18px; flex: none; }
  .details__address {
    margin-top: 28px;
    font-size: 19px; line-height: 28px; color: var(--ink-soft);
    font-style: normal;
  }
  /* Logo side */
  .card--brand {
    display: flex; align-items: center; justify-content: center;
  }
  .card--brand .brand-name { font-size: 44px; color: var(--foil); gap: 16px; }
  .card--brand .brand-mark { width: 20px; height: 20px; background: var(--foil); }
</style>
</head>
<body>
<main class="sheet">
  <section class="card card--contact" aria-label="Business card, contact side">
    <div class="brand-panel">
      <div class="brand-name"><span class="brand-mark"></span>Resinworks Hub</div>
    </div>
    <div class="details">
      <h1 class="details__name">Ted Galloway</h1>
      <ul class="details__list">
        <li class="details__item">
          <svg viewBox="0 0 24 24" fill="none" stroke="currentColor" stroke-width="2" aria-hidden="true"><path d="M5 3h4l2 5-2.5 1.5a11 11 0 0 0 6 6L16 13l5 2v4a2 2 0 0 1-2 2A16 16 0 0 1 3 5a2 2 0 0 1 2-2z"/></svg>
          604-712-3390
        </li>
        <li class="details__item">
          <svg viewBox="0 0 24 24" fill="none" stroke="currentColor" stroke-width="2" aria-hidden="true"><rect x="6" y="2" width="12" height="20" rx="2"/><line x1="11" y1="18" x2="13" y2="18"/></svg>
          604-947-2164
        </li>
        <li class="details__item">
          <svg viewBox="0 0 24 24" fill="currentColor" aria-hidden="true"><path d="M2 5h20v14H2z"/><path d="M2 5l10 8 10-8" fill="none" stroke="#0d0d0d" stroke-width="2"/></svg>
          ted@resinworkshub.ca
        </li>
      </ul>
      <address class="details__address">
        7-4812 Fernhollow Road,<br>
        Abbotsford, BC, V3K 8R2
      </address>
    </div>
  </section>

  <section class="card card--brand" aria-label="Business card, brand side">
    <div class="brand-name"><span class="brand-mark"></span>Resinworks Hub</div>
  </section>
</main>
</body>
</html>
```